SkyvornQ Business Cards and Stationary Design

Need a design for our business cards and stationary. I want to carry on the theme of the logo. I want the business cards to have a design on the back. I would like the business cards and the stationary to carry the same theme, design scheme, and branding

Target Market(s)

Airlines and Maintenance Facilities

Industry/Entity Type

Aviation

Contact Information for Business Card

Name
Position Title
Address: 4827 Trellis Hollow Road, Fort Pierce, Florida, 34951
Office Number
Mobile Number
Email
Website

Font styles to use
Serif
Sans Serif

Colors

Designer to choose colors to be used in the design.

```html
<!DOCTYPE html>
<html lang="en">
<head>
<meta charset="utf-8">
<title>SkyvornQ Business Card</title>
<link href="https://fonts.googleapis.com/css2?family=Jost:wght@400;600;700&family=Open+Sans:wght@300;400;600&display=swap" rel="stylesheet">
<style>
  :root {
    --page-bg: #e9ecef;
    --card-white: #ffffff;
    --navy: #12336b;
    --blue-deep: #0d4f95;
    --blue-mid: #0a73c4;
    --blue-bright: #1a9be3;
    --ink-grey: #555a60;
    --rule-grey: #c9ccd0;
  }
  * { margin: 0; padding: 0; box-sizing: border-box; }
  html, body { width: 1200px; height: 872px; overflow: hidden; }
  body {
    background: var(--page-bg);
    font-family: "Open Sans", Arial, sans-serif;
    position: relative;
  }
  .card {
    position: absolute;
    width: 540px;
    height: 309px;
    top: 282px;
    border-radius: 2px;
    box-shadow: 0 6px 18px rgba(0,0,0,0.18);
    overflow: hidden;
  }
  /* Back side */
  .card-back {
    left: 40px;
    background: radial-gradient(ellipse at 45% 50%, var(--blue-bright) 0%, var(--blue-mid) 45%, var(--blue-deep) 100%);
  }
  .back-mark {
    position: absolute;
    left: 50%; top: 44%;
    transform: translate(-50%, -50%);
    display: flex; flex-direction: column; align-items: center; gap: 10px;
  }
  .back-ring {
    width: 110px; height: 110px; border-radius: 50%;
    border: 9px solid rgba(9, 52, 110, 0.55);
  }
  .back-name {
    font-family: "Jost", Arial, sans-serif;
    font-weight: 600; font-size: 24px; letter-spacing: 3px;
    color: rgba(9, 52, 110, 0.75);
  }
  .back-url {
    position: absolute;
    left: 0; right: 0; bottom: 30px;
    text-align: center;
    color: #ffffff;
    font-size: 16px; letter-spacing: 4px; font-weight: 400;
  }
  /* Front side */
  .card-front {
    left: 620px;
    background: var(--card-white);
  }
  .front-mark {
    position: absolute;
    left: 28px; top: 50%;
    transform: translateY(-50%);
    width: 200px;
    display: flex; flex-direction: column; align-items: center; gap: 12px;
  }
  .front-ring {
    width: 150px; height: 150px; border-radius: 50%;
    border: 12px solid var(--blue-mid);
  }
  .front-name {
    font-family: "Jost", Arial, sans-serif;
    font-weight: 600; font-size: 22px; letter-spacing: 2px;
    color: var(--blue-deep);
  }
  .divider {
    position: absolute;
    left: 250px; top: 40px; bottom: 40px;
    width: 1px; background: var(--rule-grey);
  }
  .details {
    position: absolute;
    left: 272px; top: 38px; right: 20px;
  }
  .company {
    font-family: "Jost", Arial, sans-serif;
    font-weight: 700; font-size: 27px; letter-spacing: 5px;
    color: var(--navy); line-height: 1;
  }
  .person {
    margin-top: 18px;
    font-family: "Open Sans", Arial, sans-serif;
    font-weight: 600; font-size: 17px; color: var(--navy);
    letter-spacing: 0.2px;
  }
  .role {
    font-weight: 300; font-size: 15px; color: var(--ink-grey);
    letter-spacing: 0.5px; margin-top: 1px;
  }
  .contacts { list-style: none; margin-top: 14px; }
  .contacts li {
    display: flex; align-items: flex-start; gap: 7px;
    font-size: 12.5px; color: #2a2d31; line-height: 1.55;
  }
  .contacts li.address { margin-top: 6px; line-height: 1.45; }
  .contacts svg { flex: 0 0 12px; width: 12px; height: 12px; margin-top: 4px; }
</style>
</head>
<body>

  <section class="card card-back" aria-label="Business card back">
    <div class="back-mark">
      <div class="back-ring"></div>
      <div class="back-name">SkyvornQ</div>
    </div>
    <p class="back-url">www.skyvornq.com</p>
  </section>

  <section class="card card-front" aria-label="Business card front">
    <div class="front-mark">
      <div class="front-ring"></div>
      <div class="front-name">SkyvornQ</div>
    </div>
    <div class="divider"></div>
    <div class="details">
      <h1 class="company">SKYVORNQ</h1>
      <p class="person">MARCUS DELANE</p>
      <p class="role">PRESIDENT</p>
      <ul class="contacts">
        <li>
          <svg viewBox="0 0 12 12"><circle cx="6" cy="6" r="5.3" fill="none" stroke="#0d4f95" stroke-width="1.2"/><path d="M4 3.5l1 1.4-.6.7c.4.8 1 1.4 1.8 1.8l.7-.6 1.4 1-.6.9c-2.2-.3-4-2.1-4.3-4.3z" fill="#0d4f95"/></svg>
          <span>772-418-3096</span>
        </li>
        <li>
          <svg viewBox="0 0 12 12"><circle cx="6" cy="6" r="5.3" fill="none" stroke="#0d4f95" stroke-width="1.2"/><rect x="4.2" y="2.8" width="3.6" height="6.4" rx="0.6" fill="none" stroke="#0d4f95" stroke-width="1"/></svg>
          <span>772-905-2147</span>
        </li>
        <li>
          <svg viewBox="0 0 12 12"><circle cx="6" cy="6" r="5.3" fill="none" stroke="#0d4f95" stroke-width="1.2"/><rect x="3" y="4" width="6" height="4.2" fill="none" stroke="#0d4f95" stroke-width="0.9"/><path d="M3 4l3 2.3L9 4" fill="none" stroke="#0d4f95" stroke-width="0.9"/></svg>
          <span>info@skyvornq.com</span>
        </li>
        <li>
          <svg viewBox="0 0 12 12"><circle cx="6" cy="6" r="5.3" fill="none" stroke="#0d4f95" stroke-width="1.2"/><ellipse cx="6" cy="6" rx="2.2" ry="5.3" fill="none" stroke="#0d4f95" stroke-width="0.8"/><path d="M0.8 6h10.4" stroke="#0d4f95" stroke-width="0.8"/></svg>
          <span>www.skyvornq.com</span>
        </li>
        <li class="address">
          <svg viewBox="0 0 12 12"><path d="M6 11.2S2.2 7.2 2.2 4.6a3.8 3.8 0 0 1 7.6 0C9.8 7.2 6 11.2 6 11.2z" fill="none" stroke="#0d4f95" stroke-width="1.2"/><circle cx="6" cy="4.6" r="1.3" fill="#0d4f95"/></svg>
          <span>4827 Trellis Hollow Road,<br>Fort Pierce, Florida, 34951</span>
        </li>
      </ul>
    </div>
  </section>

</body>
</html>
```